uk based ecommerce website requires fresh look ,high quality look and feel

we are a web based company selling eco friendly ground reinforcement grids to diy and construction sectors
our existing website is www.pondermeshpaths.co.uk ,

we have already updated the logo so that is the branding sorted .so we need a ecommerce website that is very much up-to date in design and layout and which has content management system for ease of use so that we can add products and information as required.

Use current logo as reference for colour scheme.
www.pondermeshpaths.co.uk

The current website has 6 pages accessible through the navigation bar, I would now like 5 pages, removing the need for the Trade Enquiries page possibly have it with along with contact us.

Target Market(s)

construction industry , diy end users,
retail market, landscapers, gardeners

Industry/Entity Type

Construction

Font styles to use
Other font styles liked:
• logo font prometo

Colors
f78f20
9bcb3c

Requirements
Must have
• logo colours and logo design in website with cms responsive design for tablet and mobile devices
• expect content to work flawlessly and look great across all devices
• HTML 5 custom design with coding as required
• must have good experiance in ecommerce website design
• eye catching, high quality look and feel and very user friedly ,very up-to date.
Nice to have
• picture slider show
• explain in writing what exactly i am getting in my ecommerce website
Should not have
• plain , basic design , old fashion looking ,cheap look

```html
<!DOCTYPE html>
<html lang="en">
<head>
<meta charset="utf-8">
<title>Pondermesh Ground Solutions</title>
<link href="https://fonts.googleapis.com/css2?family=Lato:wght@400;700;900&display=swap" rel="stylesheet">
<style>
:root{
  --orange:#f78f20;
  --green:#9bcb3c;
  --dark:#333333;
  --charcoal:#4a4a4a;
  --text:#3a3a3a;
  --muted:#777777;
  --line:#e2e2e2;
  --footer:#ebebeb;
  --white:#ffffff;
}
*{box-sizing:border-box;margin:0;padding:0}
html,body{width:1200px;height:2711px;overflow:hidden;background:var(--white)}
body{font-family:'Lato',Arial,sans-serif;color:var(--text);position:relative}
.abs{position:absolute}
a{color:inherit;text-decoration:none}

/* top bar */
.topbar{left:0;top:0;width:1200px;height:40px;background:var(--orange)}
.topbar .phone{left:672px;top:0;height:40px;display:flex;align-items:center;gap:8px;color:var(--white);font-weight:700;font-size:16px}
.topbar .account{left:829px;top:0;height:40px;width:180px;background:var(--green);display:flex;align-items:center;justify-content:space-around;color:var(--white);font-size:13px;font-weight:700}
.topbar .account span{display:flex;align-items:center;gap:6px}
.topbar .cart{left:1012px;top:0;height:40px;width:88px;background:var(--orange);color:var(--white);display:flex;align-items:center;gap:6px;padding-left:6px;font-size:13px;font-weight:900;line-height:1}
.topbar .cart small{display:block;font-size:10px;font-weight:400}

/* header */
.brand{left:99px;top:62px;display:flex;align-items:center;gap:14px}
.brand .mark{width:60px;height:60px;background:var(--green)}
.brand .name{font-size:32px;font-weight:900;color:var(--orange);letter-spacing:.5px}
.search{left:675px;top:66px;display:flex}
.search .field{width:194px;height:31px;border:1px solid var(--line);font-size:11px;color:var(--muted);display:flex;align-items:center;padding-left:10px}
.search .go{width:36px;height:31px;background:var(--orange);display:flex;align-items:center;justify-content:center}
.messaging{left:936px;top:68px;display:flex;align-items:center;gap:10px;font-size:11px;line-height:1.2;color:var(--dark)}
.messaging b{display:block;font-size:12px}
.nav{right:100px;top:129px;display:flex;font-size:14px;font-weight:700;color:var(--dark);text-transform:uppercase}
.nav li{list-style:none;padding:0 17px;border-left:1px solid var(--line)}
.nav li:first-child{border-left:0}
.nav li:last-child{padding-right:0}
.nav .active{color:var(--orange)}

/* hero */
.hero{left:99px;top:173px;width:1002px;height:393px;background:linear-gradient(160deg,#8f9a86 0%,#6b6f69 35%,#3f403f 70%,#8a8d7e 100%)}
.hero .slide-arrow{top:181px;width:38px;height:34px;background:#2e2e2e;display:flex;align-items:center;justify-content:center}
.hero .prev{left:6px}
.hero .next{right:6px}
.hero h1{left:0;top:190px;width:1002px;text-align:center;color:var(--white);font-size:30px;font-weight:700;line-height:41px;text-shadow:0 2px 4px rgba(0,0,0,.6)}
.hero .cta{left:394px;top:287px;width:213px;height:39px;background:var(--green);color:var(--white);font-size:17px;display:flex;align-items:center;justify-content:center}

/* section headings */
.section-title{left:0;width:1200px;text-align:center;font-size:30px;font-weight:900;color:var(--dark);text-transform:uppercase}
.section-title em{font-style:normal;color:var(--orange)}
.title-rule{left:363px;width:474px;height:2px;background:var(--line)}
.title-rule::after{content:"";position:absolute;left:197px;top:0;width:80px;height:2px;background:var(--orange)}

/* categories */
.category{width:316px;height:180px}
.category .label{position:absolute;left:0;bottom:0;width:100%;height:34px;background:rgba(30,30,30,.78);color:var(--white);font-size:12px;font-weight:900;letter-spacing:.5px;padding-left:12px;display:flex;align-items:center}
.cat-1{background:linear-gradient(180deg,#8b8372,#4a4a48)}
.cat-2{background:linear-gradient(180deg,#6d6d6b,#3a3a3a)}
.cat-3{background:linear-gradient(180deg,#5a7fa8,#cfcfcf)}
.cat-4{background:linear-gradient(180deg,#8c8676,#5e5a53)}
.cat-5{background:linear-gradient(180deg,#7a7d89,#b39b7a)}
.cat-6{background:linear-gradient(180deg,#58773f,#c9b288)}
.pager-line{left:173px;top:1129px;width:856px;height:1px;background:var(--line)}
.pager{top:1117px;width:24px;height:24px;border-radius:50%;display:flex;align-items:center;justify-content:center}
.pager.left{left:577px;background:#e4e4e4}
.pager.right{left:613px;background:var(--green)}

/* side promos */
.promo{left:99px;width:213px;color:var(--white);text-align:center}
.promo .thumb{margin:14px auto 0;width:193px;height:98px}
.promo h3{font-size:19px;font-weight:700;margin-top:12px;letter-spacing:.3px}
.promo .btn{display:inline-block;margin-top:8px;background:var(--white);color:var(--dark);font-size:15px;padding:5px 16px;border:1px solid #ddd}
.promo-orange{top:1193px;height:204px;background:var(--orange)}
.promo-dark{top:1422px;height:213px;background:var(--charcoal)}
.promo-dark h3{font-size:25px;margin-top:8px}
.promo-dark p{font-size:15px;margin-top:8px}
.promo-green{top:1657px;height:246px;background:var(--green)}
.promo-green .thumb{height:100px}
.promo-green h3{font-size:18px;line-height:24px}

/* featured */
.featured-bar{left:336px;top:1193px;width:764px;height:38px}
.featured-bar span{position:absolute;left:12px;top:0;height:38px;display:flex;align-items:center;color:var(--white);font-weight:900;font-size:17px;letter-spacing:.5px}
.product{width:244px;height:320px;border:1px solid var(--line);background:var(--white);text-align:center}
.product .photo{margin:10px auto 0;width:220px;height:172px}
.product .price{color:var(--orange);font-size:19px;font-weight:700;margin-top:14px}
.product .name{font-size:13px;line-height:18px;color:var(--dark);margin-top:6px;height:36px}
.product .cart-btn{display:flex;margin:10px auto 0;width:114px;height:29px}
.product .cart-btn .lbl{background:var(--dark);color:var(--white);font-size:10px;font-weight:700;width:80px;display:flex;align-items:center;justify-content:center}
.product .cart-btn .ico{background:var(--orange);width:34px;display:flex;align-items:center;justify-content:center;clip-path:polygon(0 0,75% 0,100% 50%,75% 100%,0 100%)}
.sale{position:absolute;right:6px;top:6px;background:var(--green);color:var(--white);font-size:10px;font-weight:900;padding:3px 5px}
.p1{background:linear-gradient(180deg,#3d3d3d,#8a8a86)}
.p2{background:linear-gradient(180deg,#7d7a72,#4a4a48)}
.p3{background:linear-gradient(180deg,#6f7a56,#8f8374)}
.p4{background:linear-gradient(180deg,#4e6d2e,#9eb85c)}
.p5{background:linear-gradient(180deg,#c6c6c2,#8d8e88)}
.p6{background:linear-gradient(180deg,#cfd2d0,#5f7d32)}

/* gallery */
.gal-arrow{top:2185px;width:33px;height:33px;border-radius:50%;border:1px solid #cfcfcf;background:var(--white);display:flex;align-items:center;justify-content:center}
.tile{position:absolute}
.g1{left:99px;top:2042px;width:244px;height:307px;background:linear-gradient(180deg,#6a6a68,#8f8c85)}
.g1 .overlay{position:absolute;inset:0;background:rgba(40,40,40,.5);display:flex;flex-direction:column;align-items:center;justify-content:center;color:var(--white);font-size:19px;font-weight:700;text-align:center;line-height:24px;gap:14px}
.g2{left:352px;top:2042px;width:497px;height:144px;background:linear-gradient(180deg,#b9c6cf,#5c7d3a 60%,#3e3e3e)}
.g3{left:352px;top:2195px;width:244px;height:154px;background:linear-gradient(180deg,#d0cfc9,#3a3a3a)}
.g4{left:605px;top:2195px;width:244px;height:154px;background:linear-gradient(180deg,#6b9a45,#2f6a3a)}
.g5{left:860px;top:2042px;width:240px;height:307px;background:linear-gradient(180deg,#7fa7d8,#a0805c 60%,#b28c72)}

/* footer */
.footer{left:0;top:2403px;width:1200px;height:257px;background:var(--footer);border-top:2px solid #d7d7d7}
.footer h4{position:absolute;top:36px;font-size:19px;font-weight:700;color:var(--dark)}
.quick-title{left:99px}
.quick-list{position:absolute;left:99px;top:80px;list-style:none;font-size:12px;color:var(--dark);line-height:28.5px}
.quick-list li::before{content:"›";margin-right:8px;color:var(--muted)}
.contact-title{left:285px}
.contact-list{position:absolute;left:285px;top:80px;font-size:12px;line-height:17px;color:var(--dark);list-style:none}
.contact-list li{display:flex;gap:10px;margin-bottom:9px}
.contact-list svg{flex:none;margin-top:2px}
.map-title{left:600px}
.map{left:602px;top:80px;width:247px;height:134px;border:2px solid var(--white);background:linear-gradient(135deg,#dfe6d3,#c9d7e3 55%,#e8e3d6)}
.foot-brand{left:906px;top:70px;display:flex;align-items:center;gap:10px}
.foot-brand .mark{width:46px;height:46px;background:var(--green)}
.foot-brand .name{font-size:24px;font-weight:900;color:var(--orange)}
.social{left:940px;top:180px;display:flex;gap:8px}
.social i{display:block;width:26px;height:26px;border-radius:50%;background:var(--dark)}
.bottombar{left:0;top:2660px;width:1200px;height:51px;background:var(--orange);color:var(--white);font-size:12px}
.bottombar p{position:absolute;left:99px;top:18px}
.cards{position:absolute;left:910px;top:12px;display:flex;gap:8px}
.cards i{display:block;width:42px;height:27px;border-radius:3px;background:var(--white)}
</style>
</head>
<body>

<header>
  <div class="abs topbar">
    <div class="abs phone">
      <svg width="20" height="20" viewBox="0 0 20 20"><circle cx="10" cy="10" r="9" fill="none" stroke="#fff" stroke-width="1.6"/><path d="M7 5.5l1.6 2.2-1 1.2c.6 1.3 1.5 2.2 2.6 2.7l1.2-1 2.1 1.6-.9 1.7c-3.3-.3-6.2-3.2-6.5-6.5z" fill="#fff"/></svg>
      0123-456-7890
    </div>
    <div class="abs account">
      <span><svg width="12" height="14" viewBox="0 0 12 14"><rect x="1" y="6" width="10" height="8" fill="#fff"/><path d="M3 6V4a3 3 0 016 0v2" fill="none" stroke="#fff" stroke-width="1.6"/></svg>LOGIN</span>
      <span><svg width="14" height="14" viewBox="0 0 14 14"><rect x="1" y="1" width="12" height="12" fill="none" stroke="#fff" stroke-width="1.5"/><path d="M4 10l1-3 5-5 2 2-5 5z" fill="#fff"/></svg>SIGN UP</span>
    </div>
    <div class="abs cart">
      <svg width="24" height="20" viewBox="0 0 24 20"><path d="M1 2h4l3 11h12l2-8H7" fill="none" stroke="#fff" stroke-width="2"/><circle cx="10" cy="17" r="2" fill="#fff"/><circle cx="18" cy="17" r="2" fill="#fff"/></svg>
      <div>CART<small>(empty)</small></div>
    </div>
  </div>

  <a class="abs brand" href="#"><span class="mark"></span><span class="name">PONDERMESH</span></a>

  <div class="abs search">
    <div class="field">Enter product name</div>
    <div class="go"><svg width="16" height="16" viewBox="0 0 16 16"><circle cx="6.5" cy="6.5" r="4.5" fill="none" stroke="#fff" stroke-width="2"/><path d="M10 10l4.5 4.5" stroke="#fff" stroke-width="2.2"/></svg></div>
  </div>
  <div class="abs messaging">
    <svg width="26" height="20" viewBox="0 0 26 20"><rect x="1" y="1" width="24" height="18" fill="none" stroke="#9bcb3c" stroke-width="2"/><path d="M1 1l12 10L25 1" fill="none" stroke="#9bcb3c" stroke-width="2"/></svg>
    <div>24/7 HOUR<b>MESSAGING SERVICE</b></div>
  </div>

  <ul class="abs nav">
    <li class="active">Home</li>
    <li>About Us</li>
    <li>Ground Solutions</li>
    <li>Pondermesh</li>
    <li>Contact Us</li>
  </ul>
</header>

<section class="abs hero" role="img" aria-label="Gravel grid pathway running alongside a wooden fence in open countryside">
  <div class="abs slide-arrow prev"><svg width="12" height="14" viewBox="0 0 12 14"><path d="M9 1L3 7l6 6" fill="none" stroke="#fff" stroke-width="2.5"/></svg></div>
  <div class="abs slide-arrow next"><svg width="12" height="14" viewBox="0 0 12 14"><path d="M3 1l6 6-6 6" fill="none" stroke="#fff" stroke-width="2.5"/></svg></div>
  <h1 class="abs">We Provide Quality Products At An Affordable Price &amp;<br>Which Meets The Requirements Of Our Customers.</h1>
  <a class="abs cta" href="#">View Our Product Range</a>
</section>

<h2 class="abs section-title" style="top:610px"><em>Shop By</em> Product Category</h2>
<div class="abs title-rule" style="top:659px"></div>

<section>
  <div class="abs category cat-1" style="left:99px;top:701px" role="img" aria-label="Geotextile membrane laid over ground beside a fence"><span class="label">GEOTEXTILE MEMBRANES</span></div>
  <div class="abs category cat-2" style="left:442px;top:701px" role="img" aria-label="Hexagonal grid filled with gravel"><span class="label">LIGHT DOMESTIC DRIVEWAYS</span></div>
  <div class="abs category cat-3" style="left:785px;top:701px" role="img" aria-label="Car parked on a gravel driveway"><span class="label">HEAVY DOMESTIC DRIVEWAYS</span></div>
  <div class="abs category cat-4" style="left:99px;top:904px" role="img" aria-label="Workers laying grid panels on a commercial site"><span class="label">COMMERCIAL PARKING SYSTEM</span></div>
  <div class="abs category cat-5" style="left:442px;top:904px" role="img" aria-label="Grid parking area being filled with gravel"><span class="label">PARKING &amp; PATHWAY SYSTEMS</span></div>
  <div class="abs category cat-6" style="left:785px;top:904px" role="img" aria-label="Equestrian arena in a mountain valley"><span class="label">EQUESTRIAN GRID</span></div>
  <div class="abs pager-line"></div>
  <div class="abs pager left"><svg width="8" height="10" viewBox="0 0 8 10"><path d="M6 1L2 5l4 4" fill="none" stroke="#888" stroke-width="2"/></svg></div>
  <div class="abs pager right"><svg width="8" height="10" viewBox="0 0 8 10"><path d="M2 1l4 4-4 4" fill="none" stroke="#fff" stroke-width="2"/></svg></div>
</section>

<aside>
  <div class="abs promo promo-orange">
    <div class="thumb" style="background:linear-gradient(90deg,#c9b58a,#b8b8b8)" role="img" aria-label="Gravel beside a hexagonal grid panel"></div>
    <h3>PONDERMESH 25</h3>
    <span class="btn">Download PDF</span>
  </div>
  <div class="abs promo promo-dark">
    <svg style="margin-top:22px" width="78" height="52" viewBox="0 0 78 52"><rect x="2" y="6" width="46" height="32" rx="3" fill="#fff"/><path d="M48 16h16l10 12v10H48z" fill="#fff"/><circle cx="17" cy="42" r="7" fill="#fff" stroke="#4a4a4a" stroke-width="3"/><circle cx="60" cy="42" r="7" fill="#fff" stroke="#4a4a4a" stroke-width="3"/><text x="25" y="28" font-family="Lato,Arial,sans-serif" font-size="13" font-weight="900" fill="#4a4a4a" text-anchor="middle">FREE</text></svg>
    <h3>Free Shipping</h3>
    <p>Orders Over £ 100</p>
  </div>
  <div class="abs promo promo-green">
    <div class="thumb" style="background:linear-gradient(135deg,#2e2e2e,#f1f1f1)" role="img" aria-label="Black and white gravel grid panels"></div>
    <h3>Gravel Grid Data<br>Sheet</h3>
    <span class="btn">Download PDF</span>
  </div>
</aside>

<section>
  <div class="abs featured-bar">
    <svg class="abs" style="left:0;top:0" width="764" height="38" viewBox="0 0 764 38"><path d="M0 0h764l-14 19 14 19H0z" fill="#9bcb3c"/></svg>
    <span>FEATURED PRODUCTS</span>
  </div>

  <div class="abs product" style="left:338px;top:1243px">
    <div class="photo p1" role="img" aria-label="Bicycle wheel on gravel grid"></div>
    <div class="price">£ 11.00</div>
    <div class="name">Pondermesh 25<br>System</div>
    <div class="cart-btn"><span class="lbl">Add To Cart</span><span class="ico"><svg width="14" height="12" viewBox="0 0 14 12"><path d="M0 1h3l2 7h7l1-5H4" fill="none" stroke="#fff" stroke-width="1.6"/></svg></span></div>
  </div>
  <div class="abs product" style="left:594px;top:1243px">
    <span class="sale">SALE</span>
    <div class="photo p2" role="img" aria-label="Truck wheels on a grass and gravel grid"></div>
    <div class="price">£ 9.58</div>
    <div class="name">Meshbase 40 Paving<br>System For Grass &amp; Gravel</div>
    <div class="cart-btn"><span class="lbl">Add To Cart</span><span class="ico"><svg width="14" height="12" viewBox="0 0 14 12"><path d="M0 1h3l2 7h7l1-5H4" fill="none" stroke="#fff" stroke-width="1.6"/></svg></span></div>
  </div>
  <div class="abs product" style="left:850px;top:1243px">
    <div class="photo p3" role="img" aria-label="Steel U pin securing mesh in the ground"></div>
    <div class="price">£ 37.50</div>
    <div class="name">Steel U Pins</div>
    <div class="cart-btn"><span class="lbl">Add To Cart</span><span class="ico"><svg width="14" height="12" viewBox="0 0 14 12"><path d="M0 1h3l2 7h7l1-5H4" fill="none" stroke="#fff" stroke-width="1.6"/></svg></span></div>
  </div>
  <div class="abs product" style="left:338px;top:1585px">
    <span class="sale">SALE</span>
    <div class="photo p4" role="img" aria-label="Turf reinforcement mesh on grass"></div>
    <div class="price">£ 155.00</div>
    <div class="name">Turf Reinforcement Mesh 2 Tonne<br>Loading Per Sq M2</div>
    <div class="cart-btn"><span class="lbl">Add To Cart</span><span class="ico"><svg width="14" height="12" viewBox="0 0 14 12"><path d="M0 1h3l2 7h7l1-5H4" fill="none" stroke="#fff" stroke-width="1.6"/></svg></span></div>
  </div>
  <div class="abs product" style="left:594px;top:1585px">
    <div class="photo p5" role="img" aria-label="White hexagonal parking grid panels"></div>
    <div class="price">£ 12.50</div>
    <div class="name">Hexapath 30 Parking &amp; Pathway<br>System In White</div>
    <div class="cart-btn"><span class="lbl">Add To Cart</span><span class="ico"><svg width="14" height="12" viewBox="0 0 14 12"><path d="M0 1h3l2 7h7l1-5H4" fill="none" stroke="#fff" stroke-width="1.6"/></svg></span></div>
  </div>
  <div class="abs product" style="left:850px;top:1585px">
    <span class="sale">SALE</span>
    <div class="photo p6" role="img" aria-label="White external corner edging on lawn"></div>
    <div class="price">£ 23.33</div>
    <div class="name">External Corner Pack</div>
    <div class="cart-btn"><span class="lbl">Add To Cart</span><span class="ico"><svg width="14" height="12" viewBox="0 0 14 12"><path d="M0 1h3l2 7h7l1-5H4" fill="none" stroke="#fff" stroke-width="1.6"/></svg></span></div>
  </div>
</section>

<h2 class="abs section-title" style="top:1958px"><em>Project</em> Gallery</h2>
<div class="abs title-rule" style="top:2008px"></div>

<section>
  <div class="abs gal-arrow" style="left:45px"><svg width="8" height="12" viewBox="0 0 8 12"><path d="M6 1L2 6l4 5" fill="none" stroke="#999" stroke-width="1.8"/></svg></div>
  <div class="abs gal-arrow" style="left:1120px"><svg width="8" height="12" viewBox="0 0 8 12"><path d="M2 1l4 5-4 5" fill="none" stroke="#999" stroke-width="1.8"/></svg></div>
  <div class="tile g1" role="img" aria-label="Vehicle wheels on a white gravel grid">
    <div class="overlay">
      <svg width="36" height="36" viewBox="0 0 36 36"><circle cx="15" cy="15" r="11" fill="none" stroke="#fff" stroke-width="2.5"/><path d="M23 23l10 10M15 10v10M10 15h10" stroke="#fff" stroke-width="2.5"/></svg>
      <span>Pondermesh Path<br>White</span>
    </div>
  </div>
  <div class="tile g2" role="img" aria-label="Grid path curving beside a lawn and raised bed"></div>
  <div class="tile g3" role="img" aria-label="Black and white grid panels outside a terraced house"></div>
  <div class="tile g4" role="img" aria-label="Green grass reinforcement grid panels"></div>
  <div class="tile g5" role="img" aria-label="Finished gravel driveway in front of a house"></div>
</section>

<footer>
  <div class="abs footer">
    <h4 class="quick-title">Quick Links</h4>
    <ul class="quick-list">
      <li>Home</li><li>About Us</li><li>Ground Solutions</li><li>Pondermesh</li><li>Contact Us</li>
    </ul>
    <h4 class="contact-title">Contact Details</h4>
    <ul class="contact-list">
      <li><svg width="10" height="14" viewBox="0 0 10 14"><path d="M5 0a5 5 0 015 5c0 4-5 9-5 9S0 9 0 5a5 5 0 015-5z" fill="#9bcb3c"/><circle cx="5" cy="5" r="2" fill="#ebebeb"/></svg><span>PONDERMESH ECO SOLUTIONS LTD<br>Harlow Court, Millbrook Ind Est,<br>Northfield, NF4 2RT.</span></li>
      <li><svg width="12" height="12" viewBox="0 0 12 12"><path d="M2 1l2.5 2.5-1.3 1.6c.8 1.5 2 2.7 3.7 3.5l1.6-1.3L11 9.8 9.7 11C5 10.5 1.5 7 1 2.3z" fill="#9bcb3c"/></svg><span>0123-456-7890</span></li>
      <li><svg width="14" height="12" viewBox="0 0 14 12"><rect x="0" y="4" width="14" height="8" rx="2" fill="#9bcb3c"/><rect x="3" y="0" width="8" height="5" fill="#9bcb3c"/></svg><span>0845-000-1122</span></li>
      <li><svg width="14" height="12" viewBox="0 0 14 12"><rect x="0" y="1" width="14" height="10" fill="#9bcb3c"/><path d="M0 1l7 5 7-5" fill="none" stroke="#ebebeb" stroke-width="1.3"/></svg><span>sales@pondermeshpaths.co.uk</span></li>
    </ul>
    <h4 class="map-title">Location Map</h4>
    <div class="abs map" role="img" aria-label="Street map showing the company location"></div>
    <div class="abs foot-brand"><span class="mark"></span><span class="name">PONDERMESH</span></div>
    <div class="abs social"><i></i><i></i><i></i><i></i></div>
  </div>
  <div class="abs bottombar">
    <p>COPYRIGHT © 2016 PONDERMESH ECO SOLUTIONS LTD. ALL RIGHTS RESERVED.</p>
    <div class="cards" aria-label="Accepted payment methods"><i></i><i></i><i></i><i></i></div>
  </div>
</footer>

</body>
</html>
```